Packaging design for a reclosable bag for our product

We have a logo, and we need to put it on packaging for our product and while we want the look to be simple, we want it to follow good design principles and also contain spaces for other product descriptions.

There will be 5 sizes at launch so I'd like 5 variations, one for each size.

I've included a few mockups of the type of bag that I made but they are all just rough ideas that I had.

I want the brand to look scientific and methodical and even a bit quirky, as in "wow this is a serious product but also a bit unusual."

```html
<!DOCTYPE html>
<html lang="en">
<head>
<meta charset="utf-8">
<title>KV3 Bias Lighting – Extra Large Pouch</title>
<link rel="stylesheet" href="https://fonts.googleapis.com/css2?family=Open+Sans:wght@400;600&family=Cormorant+Garamond:ital,wght@1,500&display=swap">
<style>
  :root {
    --page: #ffffff;
    --pouch-black: #0b0b0b;
    --pouch-upper: #1c1c1c;
    --band-white: #f4f4f4;
    --band-edge: #c9c9c9;
    --ink-dark: #1a1a1a;
    --ink-light: #ededed;
    --ink-muted: #cfcfcf;
    --silver-hi: #ffffff;
    --silver-lo: #8a8a8a;
  }
  html, body {
    margin: 0;
    padding: 0;
    width: 1200px;
    height: 750px;
    overflow: hidden;
    background: var(--page);
  }
  .canvas {
    position: relative;
    width: 1200px;
    height: 750px;
    background: var(--page);
    font-family: "Open Sans", Arial, sans-serif;
  }
  .pouch {
    position: absolute;
    left: 367px;
    top: 64px;
    width: 443px;
    height: 580px;
    display: flex;
    flex-direction: column;
  }
  .pouch__brand-panel {
    height: 287px;
    background: linear-gradient(160deg, #2a2a2a 0%, var(--pouch-upper) 45%, #111 100%);
    display: flex;
    align-items: flex-end;
    justify-content: center;
    padding-bottom: 38px;
    box-sizing: border-box;
  }
  .brand-name {
    margin: 0;
    font-family: "Open Sans", Arial, sans-serif;
    font-weight: 600;
    font-size: 178px;
    line-height: 1;
    letter-spacing: -4px;
    color: var(--ink-light);
  }
  .pouch__category-band {
    height: 45px;
    background: linear-gradient(90deg, var(--band-edge) 0%, var(--band-white) 12%, var(--band-white) 88%, var(--band-edge) 100%);
    display: flex;
    align-items: center;
    justify-content: center;
  }
  .category {
    margin: 0;
    font-weight: 400;
    font-size: 28px;
    letter-spacing: 0.5px;
    color: var(--ink-dark);
  }
  .pouch__spec-panel {
    flex: 1;
    background: var(--pouch-black);
    display: flex;
    flex-direction: column;
    align-items: center;
    padding-top: 42px;
    box-sizing: border-box;
  }
  .size-label {
    margin: 0;
    font-size: 16px;
    letter-spacing: 0.6px;
    color: var(--ink-light);
  }
  .length {
    margin: 6px 0 0;
    font-family: "Cormorant Garamond", Georgia, serif;
    font-style: italic;
    font-weight: 500;
    font-size: 92px;
    line-height: 1;
    background: linear-gradient(180deg, var(--silver-hi) 10%, var(--silver-lo) 90%);
    -webkit-background-clip: text;
    background-clip: text;
    color: transparent;
  }
  .spec-lines {
    margin: 8px 0 0;
    text-align: center;
    font-size: 15px;
    line-height: 23px;
    letter-spacing: 0.4px;
    color: var(--ink-muted);
  }
</style>
</head>
<body>
  <main class="canvas">
    <section class="pouch" aria-label="Extra large bias lighting pouch">
      <header class="pouch__brand-panel">
        <h1 class="brand-name">KV3</h1>
      </header>
      <div class="pouch__category-band">
        <h2 class="category">BIAS LIGHTING</h2>
      </div>
      <div class="pouch__spec-panel">
        <p class="size-label">EXTRA LARGE</p>
        <p class="length">5m</p>
        <p class="spec-lines">6500K White Bias Lighting<br>Simulated D65 CRI 90+</p>
      </div>
    </section>
  </main>
</body>
</html>
```